I need a flyer made , the flyer can be one page or two pages or three pages . I will be posting this on Instagram and social media platforms. I am a luxury home builder , I am looking to hire a construction project manager . Below are some examples and ideas what can be on the flyer

We’re looking for a construction project manager who’s passionate about building luxury homes at the highest standards
We’re hiring construction project manager
* Experience 5+ years in residential project management with a strong portfolio of completed homes.
* location : Bergen County NJ
* excellent leadership skills, leads teams with confidence and clarity
* communicates seamlessly with architects , engineers, designers and clients
*knows how to manage budgets and timelines without compromising quality
*solves problems with a positive solution first mindset
* pays attention to every detail because in luxury the small things are the big things

Apply now , link in bio or DM to connect.

My logo is attached, my web site www.velstridebuilders.com
My style is modern but still warm and inviting. I like a clean classy look .

Please don’t add any images of chairs or people to the flyer , I do not want people on my flyer. Do not add standard images of offices and houses , we are luxury builders , we build homes over 2 million dollars. Keep a classy , simple modern look . High end .

You can add a white hard hat with my logo on it for a image , this is a suggestion does not have to be on my flyer ,

```html
<!DOCTYPE html>
<html lang="en">
<head>
<meta charset="UTF-8">
<title>Velstride Builders – We Are Hiring</title>
<link rel="stylesheet" href="https://fonts.googleapis.com/css2?family=Archivo:wdth,wght@125,800&family=Bebas+Neue&family=DM+Sans:wght@400&family=Sora:wght@400;600;700&display=swap">
<style>
  :root {
    --ink: #0d0d0d;
    --paper: #ffffff;
    --panel: #111111;
  }
  * { margin: 0; padding: 0; box-sizing: border-box; }
  html, body { width: 927px; height: 1200px; overflow: hidden; background: var(--paper); }
  .flyer { position: relative; width: 927px; height: 1200px; background: var(--paper); }
  .flyer__shapes { position: absolute; inset: 0; width: 927px; height: 1200px; }
  .abs { position: absolute; }
  .brand {
    left: 0; width: 927px; top: 212px; text-align: center;
    font-family: "Sora", sans-serif; font-weight: 600; font-size: 21px;
    letter-spacing: 2px; color: var(--ink); text-transform: uppercase;
  }
  .headline {
    left: 0; width: 927px; text-align: center;
    font-family: "Bebas Neue", sans-serif; font-size: 182px; line-height: 1;
    color: var(--ink); letter-spacing: 1px;
  }
  .headline--top { top: 285px; }
  .headline--bottom { top: 430px; }
  .role {
    left: 264px; width: 401px; top: 575px; height: 64px;
    display: flex; flex-direction: column; justify-content: center; align-items: center;
    font-family: "Archivo", sans-serif; font-stretch: 125%; font-weight: 800;
    font-size: 23px; line-height: 26px; color: var(--paper); text-transform: uppercase;
  }
  .location {
    left: 0; width: 927px; top: 640px; text-align: center;
    font-family: "Sora", sans-serif; font-weight: 700; font-size: 31px;
    color: var(--ink); letter-spacing: -0.3px;
  }
  .intro {
    left: 244px; width: 460px; top: 692px; text-align: center;
    font-family: "Sora", sans-serif; font-weight: 700; font-size: 19px; line-height: 28px;
    color: var(--paper); letter-spacing: -0.4px;
  }
  .requirements__title {
    left: 256px; top: 829px;
    font-family: "Archivo", sans-serif; font-stretch: 125%; font-weight: 800;
    font-size: 25px; color: var(--ink);
  }
  .requirements__list {
    left: 266px; top: 871px; list-style: none;
    font-family: "DM Sans", sans-serif; font-size: 13.5px; line-height: 22px;
    color: var(--ink); letter-spacing: 0.2px;
  }
  .requirements__list li { position: relative; padding-left: 13px; }
  .requirements__list li::before {
    content: ""; position: absolute; left: 0; top: 9px;
    width: 4px; height: 4px; border-radius: 50%; background: var(--ink);
  }
  .cta__label {
    left: 225px; width: 214px; top: 1023px; height: 51px;
    display: flex; align-items: center; justify-content: center;
    font-family: "Sora", sans-serif; font-weight: 700; font-size: 21px;
    letter-spacing: -0.8px; color: var(--ink);
  }
  .cta__details {
    left: 439px; width: 264px; top: 1028px; text-align: center;
    font-family: "Sora", sans-serif; font-size: 13.5px; line-height: 18px; color: var(--paper);
  }
  .cta__details strong { font-weight: 600; }
</style>
</head>
<body>
<main class="flyer">
  <svg class="flyer__shapes" viewBox="0 0 1700 2200" aria-hidden="true">
    <rect class="panel" x="94" y="122" width="1481" height="1918" fill="var(--panel)"/>
    <polyline class="roof-line" points="970,292 1046,238 1478,522" fill="none" stroke="var(--paper)" stroke-width="18" stroke-linecap="round" stroke-linejoin="round"/>
    <rect class="chimney" x="543" y="283" width="102" height="170" rx="8" fill="var(--paper)"/>
    <rect class="chimney__hole" x="565" y="303" width="58" height="130" fill="var(--panel)"/>
    <path class="house" d="M853,222 L392,512 Q378,524 395,530 L406,530 L406,1252 L1308,1252 L1308,530 L1318,530 Q1334,524 1318,512 Z" fill="var(--paper)"/>
    <rect class="role-band" x="485" y="1055" width="735" height="117" fill="var(--ink)"/>
    <rect class="requirements" x="413" y="1490" width="879" height="365" rx="20" fill="var(--paper)"/>
    <circle class="badge" cx="1217" cy="1545" r="113" fill="var(--paper)"/>
    <circle class="badge__inner" cx="1217" cy="1545" r="90" fill="var(--ink)"/>
    <g class="megaphone" fill="var(--paper)" stroke="var(--paper)" stroke-linecap="round">
      <path d="M1188,1568 L1215,1505 L1262,1552 Z" stroke-width="6" stroke-linejoin="round"/>
      <circle cx="1260" cy="1530" r="11" stroke="none"/>
      <line x1="1228" y1="1572" x2="1236" y2="1592" stroke-width="8"/>
      <line x1="1193" y1="1492" x2="1199" y2="1502" stroke-width="5"/>
      <line x1="1175" y1="1522" x2="1186" y2="1528" stroke-width="5"/>
      <line x1="1164" y1="1557" x2="1176" y2="1554" stroke-width="5"/>
    </g>
    <rect class="cta" x="413" y="1877" width="877" height="93" rx="18" fill="var(--ink)" stroke="var(--paper)" stroke-width="6"/>
    <path class="cta__button" d="M431,1877 L805,1877 L805,1970 L431,1970 Q413,1970 413,1952 L413,1895 Q413,1877 431,1877 Z" fill="var(--paper)"/>
  </svg>

  <div class="abs brand">Velstride Builders</div>
  <h1 class="abs headline headline--top">We Are</h1>
  <div class="abs headline headline--bottom">Hiring</div>
  <h2 class="abs role"><span>Construction</span><span>Project Manager</span></h2>
  <p class="abs location">Bergen County, NJ</p>
  <p class="abs intro">We’re looking for a Residential Project Manager with 5+ years experience and a strong portfolio of completed homes.</p>

  <h3 class="abs requirements__title">REQUIREMENTS:</h3>
  <ul class="abs requirements__list">
    <li>Lead teams with confidence</li>
    <li>Lead teams with confidence</li>
    <li>Communicate with architects, designers &amp; clients</li>
    <li>Manage budgets &amp; timelines without sacrificing quality</li>
    <li>Solve problems with a solution-first mindset</li>
    <li>Obsess over the details — in luxury, they matter most</li>
  </ul>

  <div class="abs cta__label">Apply Now</div>
  <p class="abs cta__details">Link in bio or DM to connect.<br><strong>info@velstridebuilders.com</strong></p>
</main>
</body>
</html>
```